Web design project for exciting Australian start-up

Background
We are looking for a creative and talented web design artist to work alongside our market leading web developer.
• You will be required to create a modern and clean design theme for our website, incorporating selected rustic colour scheme elements for our exciting Australian start-up to operate within the coffee industry.
reoccurring work to be expected to flow to the successful designer.
Requirements
• c. 5 - 10 page website
• Landing page
• Log in/ out
• 404 template
• Typography is emphasised
• Please use either a) typemarrow.com, b) free web fonts, c) brindle fonts
• All design elements in vector format
• Preferably with icons for each header title(i.e. about us, how it works etc) but designer have free reign over how the site looks, so might not be applicable
• All pages to be responsive
• Down to eSlab resolution

High level visual design brief attached - additional pages to be worked from base design.

Design inspiration
• We would like to use design elements from the following sources:
http://www.zandrix.com/halcyon/ (Functionality)
Colour scheme refer to logo and complementary style guide

```html
<!DOCTYPE html>
<html lang="en">
<head>
<meta charset="utf-8">
<title>Bean Quarter – Marketplace</title>
<link rel="stylesheet" href="https://fonts.googleapis.com/css2?family=Merriweather:wght@400;700&family=Ubuntu:wght@400;500&display=swap">
<style>
  :root {
    --page: #edecec;
    --panel: #f1f1f1;
    --white: #ffffff;
    --ink: #1b1b1b;
    --muted: #6f6a5e;
    --faint: #b3ae9f;
    --orange: #e98c26;
    --orange-dark: #c9701a;
    --orange-glow: #fbdcb8;
    --field: #e8e6dd;
    --field-edge: #d8d4c4;
    --menu: #f7f6f2;
    --menu-edge: #e3dfd2;
    --rule: #f2c79a;
  }
  * { box-sizing: border-box; margin: 0; padding: 0; }
  html, body { width: 1200px; height: 856px; overflow: hidden; }
  body { background: var(--page); font-family: "Ubuntu", sans-serif; color: var(--ink); position: relative; }
  .abs { position: absolute; }

  .site-header { left: 0; top: 0; width: 1200px; height: 133px; border-bottom: 1px solid #cfcfcf; }
  .brand { left: 180px; top: 44px; display: flex; align-items: center; gap: 12px;
    font-family: "Merriweather", serif; font-weight: 700; font-size: 30px; letter-spacing: 1px; color: var(--ink); }
  .brand-dot { width: 34px; height: 34px; border-radius: 50%; background: var(--orange); }

  .account-nav { left: 711px; top: 68px; height: 40px; display: flex; background: var(--orange);
    border-radius: 2px; box-shadow: 0 1px 2px rgba(0,0,0,.2); }
  .account-nav a { display: flex; align-items: center; padding: 0 20px; color: var(--ink); text-decoration: none;
    font-family: "Merriweather", serif; font-size: 14px; border-right: 1px solid var(--orange-dark); }
  .account-nav a:last-child { border-right: 0; }
  .account-nav a:first-child { width: 122px; justify-content: center; }
  .account-nav a:nth-child(2) { width: 98px; justify-content: center; }
  .account-nav a:last-child { width: 89px; justify-content: center; }

  .intro { left: 0; top: 134px; width: 458px; height: 517px; background: var(--white); }
  .search-panel { left: 458px; top: 134px; width: 571px; height: 517px; background: var(--panel); }
  .right-gutter { left: 1029px; top: 134px; width: 171px; height: 517px; background: var(--white); }

  .page-title { left: 196px; top: 292px; font-family: "Merriweather", serif; font-size: 31px; font-weight: 400; }

  .cta { display: flex; align-items: center; justify-content: space-between; padding: 0 16px;
    background: linear-gradient(#ee9834, #d9791c); color: #fff; font-family: "Merriweather", serif; font-weight: 700;
    font-size: 16px; letter-spacing: .3px; border: 4px solid var(--orange-glow); border-radius: 3px; text-decoration: none; }
  .cta svg { width: 26px; height: 26px; }
  .start-tender { left: 189px; top: 345px; width: 216px; height: 52px; }
  .launch-search { left: 781px; top: 568px; width: 215px; height: 52px; }

  .select { left: 482px; width: 150px; height: 29px; display: flex; background: var(--field);
    border: 1px solid var(--field-edge); border-top: 3px solid var(--field-edge); border-radius: 2px;
    box-shadow: 0 1px 2px rgba(0,0,0,.12); font-size: 11px; color: var(--muted); }
  .select span { flex: 1; padding-left: 13px; line-height: 24px; }
  .select i { width: 27px; border-left: 1px solid var(--field-edge); display: flex; align-items: center; justify-content: center; }
  .select i::after { content: ""; border: 4px solid transparent; }
  .select.open i::after { border-top: 4px solid var(--muted); margin-top: 4px; }
  .select.closed i::after { border-left: 4px solid var(--muted); margin-left: 4px; }
  .select.disabled { opacity: .55; }

  .menu { width: 146px; background: var(--menu); box-shadow: 0 1px 3px rgba(0,0,0,.18); border-radius: 2px; }
  .menu li { list-style: none; height: 27px; line-height: 27px; padding-left: 13px; font-size: 11px;
    color: var(--muted); border-bottom: 1px solid var(--menu-edge); background: #fbfbf9; }
  .menu li.active { color: var(--orange); }
  .menu li:last-child { border-bottom: 0; }

  .site-footer { left: 0; top: 651px; width: 1200px; height: 205px; border-top: 1px solid var(--rule); }
  .foot-col { top: 660px; }
  .foot-col h2 { display: flex; align-items: center; gap: 9px; font-family: "Merriweather", serif;
    font-weight: 400; font-size: 20px; margin-bottom: 14px; }
  .foot-col ul { list-style: none; padding-left: 23px; }
  .foot-col li { display: flex; align-items: center; gap: 6px; font-size: 13px; color: #2b2b2b; height: 31px; }
  .social li { gap: 8px; font-size: 11px; height: 31.5px; padding-left: 0; }
  .social ul { padding-left: 13px; }
  .soc-dot { width: 20px; height: 20px; border-radius: 50%; background: #2b2b2b; }
  .copyright { left: 0; top: 832px; width: 1200px; text-align: center; font-size: 11px; color: #2b2b2b; }
</style>
</head>
<body>
  <header class="site-header abs">
    <div class="brand abs"><span>BEAN</span><span class="brand-dot"></span><span>QUARTER</span></div>
    <nav class="account-nav abs">
      <a href="#">My account</a><a href="#">Logged in</a><a href="#">Logout</a>
    </nav>
  </header>

  <section class="intro abs"></section>
  <section class="search-panel abs"></section>
  <div class="right-gutter abs"></div>

  <h1 class="page-title abs">Marketplace</h1>
  <a href="#" class="cta start-tender abs">START A TENDER
    <svg viewBox="0 0 26 26"><path d="M4 4l8 9-8 9M13 4l8 9-8 9" fill="none" stroke="#fff" stroke-width="3"/></svg></a>

  <div class="select open abs" style="top:177px"><span>Tender Type</span><i></i></div>
  <ul class="menu abs" style="left:630px;top:184px">
    <li>One–off</li><li class="active">Recurring</li>
  </ul>
  <ul class="menu abs" style="left:776px;top:212px">
    <li>6 Months</li><li>12 Months</li>
  </ul>

  <div class="select closed abs" style="top:237px"><span>Quantity (kg)</span><i></i></div>

  <div class="select open abs" style="top:297px"><span>Wholesaler</span><i></i></div>
  <ul class="menu abs" style="left:630px;top:305px">
    <li>Marrano</li><li class="active">Del Corso</li><li>Brewlane</li><li>Castellu</li>
  </ul>
  <ul class="menu abs" style="left:776px;top:332px">
    <li>Blend A</li><li class="active">Blend B</li>
  </ul>

  <div class="select closed disabled abs" style="top:435px"><span>Machinery</span><i></i></div>
  <div class="select closed disabled abs" style="top:486px"><span>Barista Training</span><i></i></div>
  <div class="select closed disabled abs" style="top:537px"><span>Accessories</span><i></i></div>
  <div class="select closed abs" style="top:589px"><span>Promotiom Support</span><i></i></div>

  <a href="#" class="cta launch-search abs">LAUNCH SEARCH
    <svg viewBox="0 0 26 26"><path d="M4 4l8 9-8 9M13 4l8 9-8 9" fill="none" stroke="#fff" stroke-width="3"/></svg></a>

  <footer class="site-footer abs"></footer>
  <svg width="0" height="0" class="abs">
    <defs>
      <symbol id="cup" viewBox="0 0 20 20"><path d="M3 8h11v5a4 4 0 0 1-4 4H7a4 4 0 0 1-4-4z M14 9h2a2 2 0 0 1 0 4h-2" fill="#1b1b1b" stroke="#1b1b1b" stroke-width="1.2"/><path d="M7 2c-1 2 1 3 0 5M10 2c-1 2 1 3 0 5" stroke="#1b1b1b" fill="none"/></symbol>
      <symbol id="bean" viewBox="0 0 18 18"><ellipse cx="6" cy="6" rx="4" ry="5" fill="none" stroke="#2b2b2b" stroke-width="2"/><ellipse cx="11" cy="12" rx="4" ry="5" fill="none" stroke="#2b2b2b" stroke-width="2"/></symbol>
    </defs>
  </svg>

  <div class="foot-col abs" style="left:182px">
    <h2><svg width="18" height="18"><use href="#cup"/></svg>Helpful info</h2>
    <ul>
      <li><svg width="17" height="17"><use href="#bean"/></svg>About us</li>
      <li><svg width="17" height="17"><use href="#bean"/></svg>Media enquiries</li>
      <li><svg width="17" height="17"><use href="#bean"/></svg>Terms &amp; conditions</li>
      <li><svg width="17" height="17"><use href="#bean"/></svg>Privacy policy</li>
    </ul>
  </div>
  <div class="foot-col abs" style="left:459px">
    <h2><svg width="18" height="18"><use href="#cup"/></svg>Who we are</h2>
    <ul>
      <li><svg width="17" height="17"><use href="#bean"/></svg>How it works</li>
      <li><svg width="17" height="17"><use href="#bean"/></svg>FAQ</li>
      <li><svg width="17" height="17"><use href="#bean"/></svg>Contact us</li>
    </ul>
  </div>
  <div class="foot-col social abs" style="left:744px">
    <h2><svg width="18" height="18"><use href="#cup"/></svg>Follow us</h2>
    <ul>
      <li><span class="soc-dot"></span>Find us on Chatterbox</li>
      <li><span class="soc-dot"></span>Follow us on Chirper</li>
      <li><span class="soc-dot"></span>Subscribe our channel</li>
      <li><span class="soc-dot"></span>Find us on Linkhub</li>
    </ul>
  </div>

  <p class="copyright abs">Copyright © 2014 Bean Quarter</p>
</body>
</html>
```